VelkaVision.com

Complete Website Design (Godaddy) and company Branding / Logo Design. The products will sell are only done in-person and are installed. So this site does not need to be an e-commerce site. We will only be giving out information and collecting customer inquires. Website will only need to be about 3 to 5 pages.

```html
<!DOCTYPE html>
<html lang="en">
<head>
<meta charset="utf-8">
<title>VelkaVision</title>
<link href="https://fonts.googleapis.com/css2?family=Roboto:wght@400;500;700&display=swap" rel="stylesheet">
<style>
:root{
  --blue:#1a8ae0;
  --blue-deep:#1674c6;
  --orange:#e8670a;
  --ink:#222;
  --text:#444;
  --footer:#111;
  --white:#fff;
}
*{margin:0;padding:0;box-sizing:border-box}
html,body{width:1200px;height:2345px;overflow:hidden}
body{font-family:'Roboto',Arial,sans-serif;background:var(--white);color:var(--ink);position:relative}

/* header */
.site-header{position:absolute;left:0;top:0;width:1200px;height:87px;background:var(--white)}
.brand{position:absolute;font-weight:700;color:var(--blue);white-space:nowrap}
.site-header .brand{left:165px;top:20px;font-size:33px}
.main-nav{position:absolute;left:459px;top:33px;display:flex;font-size:15px;color:var(--ink)}
.main-nav span{white-space:nowrap}
.main-nav .sep{margin:0 22px}
.btn{position:absolute;display:flex;align-items:center;justify-content:center;gap:9px;color:var(--white);font-weight:700;text-transform:uppercase;border-radius:2px;font-size:15px}
.btn-orange{background:var(--orange)}
.btn-blue{background:var(--blue)}
.login{left:905px;top:22px;width:128px;height:42px}

/* hero */
.hero{position:absolute;left:0;top:87px;width:1200px;height:720px;
  background:linear-gradient(160deg,#e9ecef 0%,#cfd3d8 35%,#8f8f92 55%,#c8aa86 80%,#b88d62 100%)}
.hero-panel{position:absolute;left:276px;top:199px;width:648px;height:317px;background:rgba(70,70,70,.55)}
.hero-kicker{position:absolute;left:0;width:1200px;top:232px;text-align:center;font-size:42px;font-weight:700;color:var(--white)}
.hero-title{position:absolute;left:0;width:1200px;top:294px;text-align:center;font-size:92px;font-weight:700;color:var(--white);line-height:1}
.get-started{left:520px;top:429px;width:161px;height:47px}
.dots{position:absolute;left:560px;top:646px;display:flex;gap:9px}
.dots i{width:14px;height:14px;border:1.5px solid var(--white);border-radius:50%;display:block;position:relative}
.dots i.on::after{content:"";position:absolute;left:3px;top:3px;width:5px;height:5px;border-radius:50%;background:var(--white)}

/* about */
.about-visual{position:absolute;left:110px;top:898px;overflow:visible}
.about-title{position:absolute;left:610px;top:926px;font-size:40px;font-weight:700;color:var(--ink)}
.about-text{position:absolute;left:610px;top:975px;width:474px;font-size:15.5px;line-height:29px;color:var(--text);text-align:justify}
.learn-more{left:610px;top:1258px;width:161px;height:47px}

/* inquiries */
.inquiries{position:absolute;left:0;top:1423px;width:1200px;height:592px;
  background:radial-gradient(ellipse at 45% 45%,#2c97e4 0%,#2590e0 50%,#1c84d6 100%)}
.inquiries h2{position:absolute;left:0;width:1200px;top:72px;text-align:center;font-size:40px;font-weight:700;color:var(--white)}
.field-label{position:absolute;font-size:15.5px;font-weight:700;color:var(--white)}
.field{position:absolute;background:var(--white);border-radius:2px;font-size:14.5px;color:#555;padding:17px 0 0 19px}
.field.right{padding-left:13px}
.submit{left:524px;top:467px;width:151px;height:46px;font-size:14.5px}

/* footer */
.site-footer{position:absolute;left:0;top:2015px;width:1200px;height:330px;background:var(--footer)}
.site-footer .brand{left:0;width:1200px;text-align:center;top:93px;font-size:36px}
.footer-nav{position:absolute;left:0;width:1200px;top:147px;display:flex;justify-content:center;font-size:16px;color:var(--white)}
.footer-nav .sep{margin:0 22px}
.socials{position:absolute;left:499px;top:2210px;display:flex;gap:6px}
.socials i{display:block;width:34px;height:34px;border:1.5px solid #ccc;border-radius:50%;position:relative}
.socials i::after{content:"";position:absolute;left:12px;top:12px;width:8px;height:8px;border-radius:50%;background:#ddd}
.footer-rule{position:absolute;left:111px;top:2272px;width:977px;height:1px;background:#555}
.copyright{position:absolute;left:0;width:1200px;top:2296px;text-align:center;font-size:14.5px;color:var(--white)}
</style>
</head>
<body>

<header class="site-header">
  <div class="brand">VelkaVision</div>
  <nav class="main-nav">
    <span>Home</span><span class="sep">/</span><span>About Us</span><span class="sep">/</span><span>Services</span><span class="sep">/</span><span>Contact Us</span>
  </nav>
  <div class="btn btn-orange login">Login
    <svg width="11" height="13" viewBox="0 0 11 13"><path d="M2.5 6V4a3 3 0 0 1 6 0v2" fill="none" stroke="#fff" stroke-width="1.8"/><rect x="1" y="6" width="9" height="7" rx="1" fill="#fff"/></svg>
  </div>
</header>

<section class="hero" role="img" aria-label="Photo of a technician installing a wall-mounted television in a living room">
  <div class="hero-panel"></div>
  <div class="hero-kicker">Welcome To</div>
  <div class="hero-title">VelkaVision</div>
  <div class="btn btn-blue get-started">Get Started
    <svg width="15" height="15" viewBox="0 0 16 16"><circle cx="8" cy="8" r="8" fill="#fff"/><path d="M5 8h6M8.5 5l3 3-3 3" fill="none" stroke="#1a8ae0" stroke-width="2"/></svg>
  </div>
  <div class="dots"><i></i><i></i><i class="on"></i><i></i></div>
</section>

<section class="about">
  <svg class="about-visual" width="450" height="450" viewBox="0 0 450 450">
    <defs><linearGradient id="projector" x1="0" y1="0" x2="0" y2="1">
      <stop offset="0" stop-color="#d9d4cf"/><stop offset=".45" stop-color="#b7b4b2"/><stop offset="1" stop-color="#c9a27a"/></linearGradient></defs>
    <circle cx="220" cy="230" r="208" fill="#e8670a"/>
    <circle cx="228" cy="222" r="208" fill="#1a8ae0"/>
    <circle cx="225" cy="226" r="200" fill="#fff"/>
    <circle cx="225" cy="226" r="191" fill="url(#projector)" role="img" aria-label="Photo of a projector on a table"/>
  </svg>
  <h2 class="about-title">About Us</h2>
  <p class="about-text">Lorem ipsum dolor sit amet, consectetur adipiscing elit, sed do eiusmod tempor incididunt ut labore et dolore magna aliqua. Ut enim ad minim veniam, quis nostrud exercitation ullamco laboris nisi ut aliquip commodo consequat. Duis aute irure dolor in reprehenderit in voluptate velit esse cillum dolore eu fugiat nulla pariatur. Excepteur sint occaecat cupidatat non proident, sunt in culpa qui officia deserunt mollit anim id est laborum Lorem ipsum dolor sit amet, consectetur adipiscing elit, sed do eiusmod tempor incididunt ut labore et dolore magna aliqua. Ut enim ad minim veniam,</p>
  <div class="btn btn-orange learn-more">Learn More
    <svg width="15" height="15" viewBox="0 0 16 16"><circle cx="8" cy="8" r="8" fill="#fff"/><path d="M5 8h6M8.5 5l3 3-3 3" fill="none" stroke="#e8670a" stroke-width="2"/></svg>
  </div>
</section>

<section class="inquiries" role="img" aria-label="Blue-tinted photo of a technician connecting cables">
  <h2>Customer Inquiries</h2>
  <div class="field-label" style="left:165px;top:155px">Your Name</div>
  <div class="field" style="left:146px;top:184px;width:442px;height:50px">John Smith</div>
  <div class="field-label" style="left:616px;top:155px">Company</div>
  <div class="field right" style="left:603px;top:184px;width:450px;height:50px">ABC Company</div>
  <div class="field-label" style="left:165px;top:255px">Email Address</div>
  <div class="field" style="left:146px;top:284px;width:442px;height:50px">johnsmith@mailbox.net</div>
  <div class="field-label" style="left:616px;top:255px">Message</div>
  <div class="field right" style="left:603px;top:284px;width:450px;height:150px">What do you talk about ....</div>
  <div class="field-label" style="left:165px;top:355px">Phone</div>
  <div class="field" style="left:146px;top:384px;width:442px;height:50px">1 888 888 888</div>
  <div class="btn btn-orange submit">Submit Now
    <svg width="14" height="14" viewBox="0 0 16 16"><circle cx="8" cy="8" r="8" fill="#fff"/><path d="M5 8h6M8.5 5l3 3-3 3" fill="none" stroke="#e8670a" stroke-width="2"/></svg>
  </div>
</section>

<footer class="site-footer">
  <div class="brand">VelkaVision</div>
  <nav class="footer-nav">
    <span>Home</span><span class="sep">/</span><span>About Us</span><span class="sep">/</span><span>Services</span><span class="sep">/</span><span>Contact Us</span>
  </nav>
</footer>
<div class="socials"><i></i><i></i><i></i><i></i></div>
<div class="footer-rule"></div>
<div class="copyright">© 2024 VelkaVision. All Rights Reserved</div>

</body>
</html>
```